Computer consultant business card

Tovric Software is a newly started computer consulting company. It's a small one-man company that provides mostly Vornix applications but also websites in collaboration with designers. I'm running this company on the side of full time university studies.

I want the final design to be clean and memorable. Be creative! :)

Some inspiration:
http://www.pixelmarta.com/design/48317
http://www.pixelmarta.com/design/2739164/business-card-design-by-frostlynk
http://www.pixelmarta.com/design/604281/business-card-design-by-koralind-vestrabanu

See attachment for my company logo.
Updates

I would like to thank everyone for submitting! I'll need a couple of days to review and ultimately select a design.

Target Market(s)

Non-technical entrepreneurs and small companies.

Industry/Entity Type

University

Requirements
Must have
• My company logo.
In any way, both colors from my logo.
First- and last name, e-mail and phone number.
Double-sided design.
Nice to have
• Something creative with the symbol in my logo

```html
<!DOCTYPE html>
<html lang="en">
<head>
<meta charset="utf-8">
<title>Tovric Software – Business Card Set</title>
<link rel="stylesheet" href="https://fonts.googleapis.com/css2?family=Questrial&family=Open+Sans:wght@400;600;700&display=swap">
<style>
  :root {
    --ink: #333333;
    --blue: #4a72b8;
    --white: #ffffff;
    --sheet: #b08a5e;
    --label: #1e1a16;
    --black: #050505;
    --slate-top: #2f3137;
    --slate-bottom: #485a84;
    --grey-text: #555555;
  }
  * { margin: 0; padding: 0; box-sizing: border-box; }
  html, body { width: 1200px; height: 788px; overflow: hidden; }
  body {
    position: relative;
    background: var(--sheet);
    font-family: "Questrial", "Century Gothic", sans-serif;
  }
  .view-label {
    position: absolute;
    width: 525px;
    text-align: center;
    font-family: "Open Sans", Arial, sans-serif;
    font-size: 20px;
    color: var(--label);
  }
  .card {
    position: absolute;
    width: 525px;
    height: 300px;
    border-radius: 22px;
    overflow: hidden;
    box-shadow: 0 3px 8px rgba(0,0,0,0.35);
  }
  .card--white { background: var(--white); }
  .card--black { background: var(--black); }
  .card--slate { background: radial-gradient(ellipse at 50% 100%, var(--slate-bottom) 0%, var(--slate-top) 85%); }

  .brand { position: absolute; display: flex; align-items: center; white-space: nowrap; }
  .brand__dot { border-radius: 50%; background: var(--blue); flex: none; }
  .brand__name { line-height: 1; font-weight: 400; }
  .brand--dark .brand__name { color: var(--ink); }
  .brand--light .brand__name { color: var(--white); }

  .front .brand { left: 34px; top: 110px; }
  .front .brand__dot { width: 68px; height: 68px; margin-right: 14px; }
  .front .brand__name { font-size: 46px; margin-top: -4px; }

  .divider {
    position: absolute; left: 269px; top: 82px; width: 2px; height: 118px;
    background: linear-gradient(to bottom, rgba(51,51,51,0), var(--ink) 30%, var(--ink) 70%, rgba(51,51,51,0));
  }
  .contact {
    position: absolute; left: 292px; top: 122px;
    font-family: "Open Sans", Arial, sans-serif; font-size: 15px; color: var(--ink);
    line-height: 24px;
  }
  .contact b { font-style: italic; font-weight: 700; }
  .name-band {
    position: absolute; left: 0; bottom: 0; width: 100%; height: 37px;
    background: var(--blue); color: var(--white);
    display: flex; align-items: center; justify-content: center;
    font-family: "Open Sans", Arial, sans-serif;
  }
  .name-band__name { font-size: 17px; font-weight: 700; }
  .name-band__role { font-size: 13px; margin-left: 6px; }

  .back .brand { left: 103px; top: 92px; }
  .back .brand__dot { width: 106px; height: 106px; margin-right: 24px; }
  .back .brand__name { font-size: 80px; margin-top: -8px; }

  .website {
    position: absolute; left: 0; width: 100%; text-align: center;
    font-size: 19px; letter-spacing: 4px;
  }
  .card--white .website { top: 248px; color: var(--grey-text); }
  .card--black .website, .card--slate .website { top: 256px; color: var(--white); }

  .texture {
    position: absolute;
    background: radial-gradient(circle, rgba(150,140,140,0.35) 0%, rgba(60,60,60,0.15) 50%, rgba(0,0,0,0) 75%);
  }
  .texture--top { left: 0; top: -60px; width: 320px; height: 200px; }
  .texture--bottom { right: 40px; bottom: -50px; width: 260px; height: 200px; }
</style>
</head>
<body>
  <div class="view-label" style="left:56px; top:33px;">Front</div>
  <div class="view-label" style="left:622px; top:33px;">Back - 1</div>
  <div class="view-label" style="left:53px; top:404px;">Back - 2</div>
  <div class="view-label" style="left:622px; top:404px;">Back - 3</div>

  <section class="card card--white front" style="left:56px; top:74px;">
    <div class="brand brand--dark">
      <span class="brand__dot"></span>
      <span class="brand__name">tovric</span>
    </div>
    <div class="divider"></div>
    <div class="contact">
      <p><b>p</b> : +12 345 6789</p>
      <p><b>e</b> : info@website.com</p>
    </div>
    <div class="name-band">
      <span class="name-band__name">First Name Last Name,</span>
      <span class="name-band__role">Designation</span>
    </div>
  </section>

  <section class="card card--white back" style="left:622px; top:74px;">
    <div class="brand brand--dark">
      <span class="brand__dot"></span>
      <span class="brand__name">tovric</span>
    </div>
    <p class="website">www.website.com</p>
  </section>

  <section class="card card--black back" style="left:53px; top:445px;">
    <div class="texture texture--top" role="img" aria-label="Perforated metal dot pattern"></div>
    <div class="texture texture--bottom" role="img" aria-label="Perforated metal dot pattern"></div>
    <div class="brand brand--light">
      <span class="brand__dot"></span>
      <span class="brand__name">tovric</span>
    </div>
    <p class="website">www.website.com</p>
  </section>

  <section class="card card--slate back" style="left:622px; top:445px;">
    <div class="brand brand--light">
      <span class="brand__dot"></span>
      <span class="brand__name">tovric</span>
    </div>
    <p class="website">www.website.com</p>
  </section>
</body>
</html>
```